Solar and battery company needs a mailer brochure

I need a Tri-fold brochure to be mailed the size of the brochure should be 16 inches long by 8.5 inches tall high gloss finish thick paper
use a solid black background the letters should be white in color and when using borders please use red color
first page to say:
BEAT BLACKOUTS SAVE MONEY
You may qualify for a free battery system.
( include a design of the utility grid , solar panels ,battery ,money sign savings just like the PDF File show it )
at the bottom of page include Prime Volt 2 Go logo and phone number 818-555-0147
please use Knullshock fonts for the upper case letters and lower case letters as well attached is the link for the Comet Forge website for inspiration https://www.cometforgeusa.example/space-systems/solar/

Target Market(s)

residential solar clients

Industry/Entity Type

solar

Font styles to use
Other font styles liked:
• Knullshock

Colors

Designer to choose colors to be used in the design.

Requirements
Must have
• Knullshock Fonts inspired by Comet Forges website https://www.cometforgeusa.example/space-systems/solar/
Nice to have
• I would like to see a black background with white Knullshock lettering CAPITAL LETTERS and lower case letters
Should not have
• should not have solar panel images ,people get turn off if they see solar panels but they like batteries around here

```html
<!DOCTYPE html>
<html lang="en">
<head>
<meta charset="utf-8">
<title>Prime Volt 2 Go – Tri-fold Mailer</title>
<link rel="stylesheet" href="https://fonts.googleapis.com/css2?family=Michroma&family=Open+Sans:wght@400;600;700&display=swap">
<style>
:root{
  --stage:#c9d3cf;
  --ink:#0b0b0c;
  --panel:#1b1b1d;
  --panel-soft:#2a2a2d;
  --white:#ffffff;
  --muted:#b9b9bd;
  --red:#e3141c;
  --yellow:#e4e01c;
  --display:"Michroma",sans-serif;
  --body:"Open Sans",sans-serif;
}
*{box-sizing:border-box;margin:0;padding:0}
html,body{width:800px;height:1200px;overflow:hidden;background:var(--stage)}
body{position:relative;font-family:var(--body);color:var(--white)}
.spread{position:absolute;left:20px;width:760px;height:404px;display:grid;grid-template-columns:repeat(3,1fr);background:var(--ink);box-shadow:0 10px 24px rgba(0,0,0,.18)}
.spread--outside{top:170px}
.spread--inside{top:626px}
.panel{position:relative;overflow:hidden;padding:30px 22px}
.panel + .panel{border-left:1px solid #000}
.panel--grey{background:linear-gradient(160deg,var(--panel-soft),var(--panel))}
.panel--black{background:var(--ink)}
.rule{position:absolute;left:0;right:0;height:2px;background:var(--red);z-index:2}
.rule--top{top:14px}
.rule--bottom{bottom:14px}
.display{font-family:var(--display);text-transform:uppercase;letter-spacing:.5px;line-height:1.2}
.copy{font-size:6.4px;line-height:1.55;color:var(--muted)}
.copy p + p{margin-top:5px}

/* outside – responsibility */
.resp-title{font-size:12px;text-align:center;margin-top:14px}
.resp-copy{margin-top:12px;text-align:center}
.partners-title{position:absolute;left:0;right:0;top:228px;text-align:center;font-size:10px}
.partners-band{position:absolute;left:0;right:0;top:250px;height:120px;background:var(--white);display:grid;grid-template-columns:repeat(3,1fr);align-items:center;justify-items:center;padding:10px 24px}
.partner-badge{width:44px;height:18px;border-radius:3px;background:#d5d8dd}
.partner-badge--round{width:22px;height:22px;border-radius:50%}

/* outside – mailing */
.stamp-box{position:absolute;top:46px;right:30px;width:44px;height:44px;border:1px solid #55555a}
.contact-list{position:absolute;left:26px;bottom:58px;list-style:none;font-size:7px;color:var(--muted)}
.contact-list li{display:flex;align-items:center;gap:7px;margin-top:6px}
.contact-list svg{width:9px;height:9px;flex:none}

/* outside – cover */
.cover-title{text-align:center;font-size:14px;line-height:1.3;margin-top:10px}
.cover-art{display:block;margin:14px auto 0;width:170px;height:170px;background:radial-gradient(circle at 50% 45%,#f4f6f5 0,#e2e6e5 60%,#cfd5d3 100%)}
.cover-foot{position:absolute;left:22px;right:22px;bottom:26px;display:grid;grid-template-columns:auto 1fr;gap:10px;align-items:center}
.brand{display:flex;flex-direction:column;align-items:center;gap:3px;font-family:var(--display);font-size:5px;text-transform:uppercase}
.brand-dot{width:22px;height:22px;border-radius:50%;background:var(--white)}
.cover-offer{font-family:var(--display);text-transform:uppercase;font-size:8.5px;line-height:1.35;text-align:center}
.cover-phone{grid-column:1 / -1;display:flex;align-items:center;justify-content:center;gap:6px;font-size:7.5px;color:var(--muted);font-family:var(--display)}

/* inside – services */
.services-title{font-size:17px;margin-top:2px}
.service{display:grid;grid-template-columns:30px 1fr;gap:8px;align-items:center;margin-top:10px}
.service-photo{width:30px;height:30px;border-radius:50%}
.service-photo--install{background:linear-gradient(135deg,#7d8fa6,#8b6a4a)}
.service-photo--storage{background:linear-gradient(135deg,#f1f1f1,#9aa0a6)}
.service-photo--commercial{background:linear-gradient(135deg,#5d7fa8,#2f4058)}
.service-name{font-size:7.5px}
.steps{display:grid;grid-template-columns:1fr 1fr;gap:2px 8px;margin-top:6px;list-style:none}
.service-copy{margin-top:5px}

/* inside – benefits */
.benefits-title{font-size:10.5px;line-height:1.35}
.benefits-intro{margin-top:6px}
.benefits-sub{font-size:9.5px;margin-top:12px}
.benefit-grid{display:grid;grid-template-columns:1fr 1fr;gap:9px 12px;margin-top:10px}
.benefit{display:grid;grid-template-columns:16px 1fr;gap:6px;align-items:center;font-size:5.8px;line-height:1.4;color:var(--muted);padding-bottom:6px;border-bottom:1px dotted #4a4a4f}
.benefit-icon{width:16px;height:16px}
.benefits-photo{position:absolute;left:22px;right:22px;bottom:26px;height:92px;background:linear-gradient(120deg,#2a3b6a 0%,#7c8aa8 35%,#c98a3c 70%,#6b3e1c 100%)}

/* inside – about */
.about-photo{position:absolute;top:16px;left:0;right:0;height:112px;background:linear-gradient(150deg,#0c1e4d 0%,#2a4c9a 45%,#9fb1d4 70%,#1a2340 100%)}
.about-body{margin-top:106px}
.about-title{font-size:11px}
.about-copy{margin-top:7px}
.about-copy strong{color:var(--white);font-weight:700}
</style>
</head>
<body>

<section class="spread spread--outside">
  <article class="panel panel--grey panel-responsibility">
    <span class="rule rule--top"></span>
    <h2 class="display resp-title">Our<br>Responsebility</h2>
    <div class="copy resp-copy">
      <p>Prime Volt 2 Go is a pioneer in the solar energy revolution. We only provide the most efficient, superior quality, American made energy products to our customers.</p>
      <p>For over a decade our goal has been to bring the most affordable systems to homes while keeping reliability at the centre of every design.</p>
      <p>Our reputation is built on trust, so we stand behind every system with care and long warranties.</p>
    </div>
    <h3 class="display partners-title">Our Partners</h3>
    <div class="partners-band">
      <span class="partner-badge partner-badge--round"></span>
      <span class="partner-badge"></span>
      <span class="partner-badge"></span>
      <span class="partner-badge"></span>
      <span class="partner-badge partner-badge--round"></span>
      <span class="partner-badge"></span>
    </div>
    <span class="rule rule--bottom"></span>
  </article>

  <article class="panel panel--grey panel-mailing">
    <span class="rule rule--top"></span>
    <div class="stamp-box"></div>
    <ul class="contact-list">
      <li><svg viewBox="0 0 10 10"><path d="M2 1h2l1 2-1 1a5 5 0 0 0 2 2l1-1 2 1v2a1 1 0 0 1-1 1A8 8 0 0 1 1 2a1 1 0 0 1 1-1z" fill="none" stroke="#b9b9bd" stroke-width=".8"/></svg>818-555-0147</li>
      <li><svg viewBox="0 0 10 10"><path d="M2 1h2l1 2-1 1a5 5 0 0 0 2 2l1-1 2 1v2a1 1 0 0 1-1 1A8 8 0 0 1 1 2a1 1 0 0 1 1-1z" fill="none" stroke="#b9b9bd" stroke-width=".8"/></svg>818-555-0192</li>
      <li><svg viewBox="0 0 10 10"><path d="M5 9S2 6 2 4a3 3 0 0 1 6 0c0 2-3 5-3 5z" fill="none" stroke="#b9b9bd" stroke-width=".8"/><circle cx="5" cy="4" r="1" fill="#b9b9bd"/></svg>7731 Cedar Row, Suite 12<br>Fairhaven OR 97801</li>
      <li><svg viewBox="0 0 10 10"><circle cx="5" cy="5" r="4" fill="none" stroke="#b9b9bd" stroke-width=".8"/><path d="M1 5h8M5 1c-2 2-2 6 0 8M5 1c2 2 2 6 0 8" fill="none" stroke="#b9b9bd" stroke-width=".6"/></svg>www.primevolt2go.example</li>
    </ul>
    <span class="rule rule--bottom"></span>
  </article>

  <article class="panel panel--black panel-cover">
    <span class="rule rule--top"></span>
    <h1 class="display cover-title">Beat Blackouts<br>Save<br>Your Money</h1>
    <div class="cover-art" role="img" aria-label="Illustration of a home with battery storage, wind turbine and electric car linked to the grid"></div>
    <div class="cover-foot">
      <div class="brand"><span class="brand-dot"></span>Prime Volt 2 Go</div>
      <p class="cover-offer">You may qualify<br>for a free<br>battery system</p>
      <p class="cover-phone"><svg width="8" height="8" viewBox="0 0 10 10"><path d="M2 1h2l1 2-1 1a5 5 0 0 0 2 2l1-1 2 1v2a1 1 0 0 1-1 1A8 8 0 0 1 1 2a1 1 0 0 1 1-1z" fill="none" stroke="#b9b9bd" stroke-width=".8"/></svg>818-555-0147</p>
    </div>
    <span class="rule rule--bottom"></span>
  </article>
</section>

<section class="spread spread--inside">
  <article class="panel panel--grey panel-services">
    <span class="rule rule--top"></span>
    <h2 class="display services-title">Services</h2>

    <div class="service">
      <span class="service-photo service-photo--install" role="img" aria-label="Photo of a solar installation crew on a roof"></span>
      <h3 class="display service-name">Solar<br>Installation</h3>
    </div>
    <ol class="steps copy">
      <li>1. Understand your energy needs</li><li>5. Obtain permitting</li>
      <li>2. Discuss your options on savings</li><li>6. Installation of system</li>
      <li>3. Conduct a site analysis</li><li>7. Final inspection</li>
      <li>4. Sign the agreement</li><li>8. Permission to operate</li>
      <li></li><li>9. Enjoy solar energy</li>
    </ol>

    <div class="service">
      <span class="service-photo service-photo--storage" role="img" aria-label="Photo of a wall-mounted home battery"></span>
      <h3 class="display service-name">Storage<br>Batteries</h3>
    </div>
    <p class="copy service-copy">Energy storage for going off-grid and rate optimizer consumption. A home battery stores energy so you can use it day or night to self power your home. It can provide backup power by itself or integrate with solar to give your home reliable clean energy 24/7.</p>

    <div class="service">
      <span class="service-photo service-photo--commercial" role="img" aria-label="Photo of a commercial rooftop array"></span>
      <h3 class="display service-name">Commercial<br>Solar</h3>
    </div>
    <p class="copy service-copy">We maximize the value of client resources through commercial financing and PPA options for businesses, schools and the public sector. Through our preferred partners we identify the best solution for your organization, letting you finance your project on or off balance sheet.</p>
    <span class="rule rule--bottom"></span>
  </article>

  <article class="panel panel--grey panel-benefits">
    <span class="rule rule--top"></span>
    <h2 class="display benefits-title">Your Solar Paanels<br>Can Do More For You</h2>
    <p class="copy benefits-intro">Adding a battery to your home lets you prevent power outages and save money every month. Even better, you may qualify for a free battery system from the state.</p>
    <h3 class="display benefits-sub">All the benefits.</h3>
    <div class="benefit-grid">
      <div class="benefit"><svg class="benefit-icon" viewBox="0 0 16 16"><circle cx="8" cy="8" r="8" fill="#e4e01c"/><path d="M4.5 8.2l2.3 2.3 4.7-4.7" fill="none" stroke="#0b0b0c" stroke-width="1.4"/></svg>24/7 backup energy ready for a blackout emergency</div>
      <div class="benefit"><svg class="benefit-icon" viewBox="0 0 16 16"><circle cx="8" cy="8" r="8" fill="#e4e01c"/><path d="M4.5 8.2l2.3 2.3 4.7-4.7" fill="none" stroke="#0b0b0c" stroke-width="1.4"/></svg>Very low maintenance, uses the sun to charge the system</div>
      <div class="benefit"><svg class="benefit-icon" viewBox="0 0 16 16"><circle cx="8" cy="8" r="8" fill="#e4e01c"/><path d="M4.5 8.2l2.3 2.3 4.7-4.7" fill="none" stroke="#0b0b0c" stroke-width="1.4"/></svg>Noiseless backup energy unlike generators</div>
      <div class="benefit"><svg class="benefit-icon" viewBox="0 0 16 16"><circle cx="8" cy="8" r="8" fill="#e4e01c"/><path d="M4.5 8.2l2.3 2.3 4.7-4.7" fill="none" stroke="#0b0b0c" stroke-width="1.4"/></svg>Weather resistant and family friendly</div>
      <div class="benefit"><svg class="benefit-icon" viewBox="0 0 16 16"><circle cx="8" cy="8" r="8" fill="#e4e01c"/><path d="M4.5 8.2l2.3 2.3 4.7-4.7" fill="none" stroke="#0b0b0c" stroke-width="1.4"/></svg>A custom system with app monitoring for real savings</div>
      <div class="benefit"><svg class="benefit-icon" viewBox="0 0 16 16"><circle cx="8" cy="8" r="8" fill="#e4e01c"/><path d="M4.5 8.2l2.3 2.3 4.7-4.7" fill="none" stroke="#0b0b0c" stroke-width="1.4"/></svg>Great energy independence from utility rate changes</div>
    </div>
    <div class="benefits-photo" role="img" aria-label="Photo of a hand using a calculator beside stacks of coins"></div>
    <span class="rule rule--bottom"></span>
  </article>

  <article class="panel panel--black panel-about">
    <div class="about-photo" role="img" aria-label="Photo of a technician fastening a panel with a power drill"></div>
    <span class="rule rule--top"></span>
    <div class="about-body">
      <h2 class="display about-title">Hi! We're Prime Volt</h2>
      <div class="copy about-copy">
        <p>Our knowledgeable consultants will give you the right financing program tailored to your needs. Our experienced installers make your installation an enjoyable experience.</p>
        <p><strong>First</strong>, you will get a free no obligation consultation, then we explain your options and give an offer that secures your energy cost for the next 25 to 30 yrs.</p>
        <p><strong>Second</strong>, you will find plenty of guarantees and warranties that protect you and your home.</p>
        <p><strong>Third</strong>, an expert engineer will design your power system based on your roof dimensions and energy needs.</p>
        <p><strong>After that</strong> you can sit back and watch our professional installers in action and see how it all comes together.</p>
        <p><strong>At last</strong> after the final inspection you get to flip the switch and start producing clean renewable energy for years to come!</p>
      </div>
    </div>
    <span class="rule rule--bottom"></span>
  </article>
</section>

</body>
</html>
```